Construction company business card

One side to be the logo with the company name, The other side I would like: (Tomas verbick) Project manager 41 barrow crescent hallam 52917306224783(03) 9703 2428Info@gudeljgroup.comAnd then maybe a couple dot points saying what we do:Construction (commercial & industrial) Civil construction

Anything else please contact me!
Maybe curved st one edge of the card

Target Market(s)

Older clientele

Industry/Entity Type

Construction Company

Contact Information for Business Card

Read above

Colors
3277b5
1b1b1b
9d9d9d

Requirements
Must have
• Use my logo on one side
Nice to have
• Read above
Should not have
• Read above

```html
<!DOCTYPE html>
<html lang="en">
<head>
<meta charset="utf-8">
<title>Stonevale Property Group – Business Card</title>
<link href="https://fonts.googleapis.com/css2?family=Lato:wght@400;700;900&display=swap" rel="stylesheet">
<style>
  :root {
    --brand-blue: #3277b5;
    --ink: #1b1b1b;
    --text-grey: #4f4f4f;
    --brand-grey: #9d9d9d;
    --card-white: #ffffff;
    --backdrop: #e7e4e0;
  }
  * { margin: 0; padding: 0; box-sizing: border-box; }
  html, body {
    width: 1200px; height: 900px; overflow: hidden;
    background: var(--backdrop);
    font-family: "Lato", sans-serif;
  }
  .stage { position: relative; width: 1200px; height: 900px; }
  .card {
    position: absolute;
    width: 556px; height: 343px;
    box-shadow: 2px 3px 6px rgba(0,0,0,0.25);
  }
  .card--front { left: 330px; top: 90px; background: var(--card-white); }
  .card--back { left: 330px; top: 469px; background: var(--brand-blue);
    display: flex; align-items: center; justify-content: center; }

  .holder { position: absolute; left: 34px; top: 40px; }
  .holder__name {
    color: var(--brand-blue); font-weight: 700; font-size: 22px;
    letter-spacing: 0.3px; text-transform: uppercase; line-height: 1.1;
  }
  .holder__role { color: var(--text-grey); font-size: 15px; line-height: 1.2; }

  .brand {
    position: absolute; right: 34px; top: 35px; width: 202px;
    display: flex; flex-direction: column; align-items: center; gap: 16px;
  }
  .brand__dot { width: 94px; height: 94px; border-radius: 50%; background: var(--brand-blue); }
  .brand__name {
    color: var(--brand-blue); font-weight: 900; font-size: 30px;
    text-transform: uppercase; letter-spacing: 1px; text-align: center; line-height: 1;
  }
  .brand__name small { display: block; font-size: 11px; letter-spacing: 4.5px; margin-top: 3px; }

  .contact { position: absolute; left: 33px; top: 226px; list-style: none;
    color: var(--text-grey); font-size: 15px; }
  .contact li { display: flex; align-items: center; gap: 4px; height: 20.5px; }
  .contact li.contact__address { margin-top: 7px; }
  .contact svg { width: 13px; height: 13px; fill: var(--brand-blue); flex: none; }

  .services { position: absolute; right: 52px; top: 254px; list-style: none;
    color: var(--text-grey); font-size: 15px; text-align: right; line-height: 20.5px; }
  .services li.has-dot { position: relative; }
  .services li.has-dot::after {
    content: ""; position: absolute; right: -12px; top: 6px;
    width: 9px; height: 9px; border-radius: 50%; background: var(--brand-blue);
  }

  .back-brand {
    color: var(--card-white); font-weight: 900; font-size: 34px;
    text-transform: uppercase; letter-spacing: 2px; text-align: center; line-height: 1.1;
  }
  .back-brand small { display: block; font-size: 14px; letter-spacing: 5px; }
</style>
</head>
<body>
<main class="stage">
  <section class="card card--front">
    <div class="holder">
      <h1 class="holder__name">Tomas Verbick</h1>
      <p class="holder__role">Project manager</p>
    </div>

    <div class="brand">
      <span class="brand__dot"></span>
      <p class="brand__name">Stonevale<small>Property Group</small></p>
    </div>

    <ul class="contact">
      <li><svg viewBox="0 0 16 16"><path d="M2 6c0-2 2-3 6-3s6 1 6 3v1h-3V5.5H5V7H2zM4 8h8l1.5 5h-11z"/></svg>7306224783</li>
      <li><svg viewBox="0 0 16 16"><path d="M4 1h8v14H4zM5.5 2.5v9h5v-9zM7.2 12.5h1.6v1.2H7.2z"/></svg>(03) 9418 6573</li>
      <li><svg viewBox="0 0 16 16"><path d="M1 3h14v10H1zM2.5 4.5 8 9l5.5-4.5z"/></svg>Info@verbickgroup.com</li>
      <li class="contact__address"><svg viewBox="0 0 16 16"><path d="M8 0a5 5 0 0 1 5 5c0 4-5 11-5 11S3 9 3 5a5 5 0 0 1 5-5zm0 3a2 2 0 1 0 0 4 2 2 0 0 0 0-4z"/></svg>41 barrow crescent kelmore 5291</li>
    </ul>

    <ul class="services">
      <li class="has-dot">Construction</li>
      <li>(commercial &amp; industrial)</li>
      <li class="has-dot">Civil construction</li>
    </ul>
  </section>

  <section class="card card--back">
    <p class="back-brand">Stonevale<small>Property Group</small></p>
  </section>
</main>
</body>
</html>
```